We are a local Communty Pharmacy wishing to promote and market a specialised Pharmaceutical Service

We would like a design that is professional and enticing ( according to the brief In attached files)
We wish to Market Compounding Pharmacy as a specialist side of our business.
We have the expertise a purpose built preparation laboratory.
The main purpose is an Internet presence that entices prospective patients to contact or visit our physical store.

Target Market(s)

Patients Medicos and Veterinary clients

Industry/Entity Type

Pharmacy

Coding

Coded - Design and coding required

Number of Pages Required

1 page

Requirements
Must have
• Clear friendly image
Nice to have
• soft enticing feel
Should not have
• No crass loud unprofessional elements

```html
<!DOCTYPE html>
<html lang="en">
<head>
<meta charset="utf-8">
<title>Greenway Compounding</title>
<link href="https://fonts.googleapis.com/css2?family=Open+Sans:wght@300;400;600;700&display=swap" rel="stylesheet">
<style>
:root{
  --blue:#1b8fd0;
  --blue-dark:#1576ad;
  --slate:#2f3640;
  --slate-2:#3a424d;
  --ink:#3c3c3c;
  --muted:#6f757c;
  --rule:#e3e6ea;
  --footer:#24282e;
  --footer-2:#1a1d21;
  --white:#ffffff;
}
*{box-sizing:border-box;margin:0;padding:0}
html,body{width:769px;height:1200px;overflow:hidden}
body{font-family:"Open Sans",Arial,sans-serif;color:var(--ink);background:var(--white);position:relative}
a{color:inherit;text-decoration:none}

.topbar{height:30px;border-bottom:1px solid var(--rule);display:flex;justify-content:flex-end;align-items:center;padding-right:40px;font-size:8px;color:var(--muted);letter-spacing:.5px}
.topbar span{margin:0 4px}

.header{height:68px;display:flex;justify-content:space-between;align-items:stretch;padding:0 40px 0 70px}
.brand{display:flex;align-items:center;gap:8px}
.brand-dot{width:20px;height:20px;border-radius:50%;background:var(--blue)}
.brand-name{font-size:16px;font-weight:700;color:var(--blue);text-transform:uppercase;letter-spacing:.3px}
.nav{display:flex;align-items:stretch}
.nav a{display:flex;flex-direction:column;justify-content:flex-end;align-items:center;padding:0 13px 14px;font-size:8px;font-weight:600;color:var(--ink);letter-spacing:.5px}
.nav a.active{background:var(--blue);color:var(--white)}
.nav a.active svg{margin-bottom:6px}

.hero{position:relative;height:377px}
.hero-photo{position:absolute;inset:0;background:linear-gradient(100deg,#eef2f6 0%,#d9e0e8 35%,#c9a7ab 60%,#b3434a 80%,#8e2a33 100%)}
.hero-copy{position:absolute;left:82px;top:165px;width:300px}
.hero-copy p{background:rgba(255,255,255,.9);color:var(--blue-dark);font-size:10px;line-height:16px;padding:8px 10px;text-transform:uppercase}
.btn{display:inline-block;margin-top:10px;background:var(--blue);color:var(--white);font-size:9px;font-weight:600;padding:9px 14px;letter-spacing:.5px}
.arrow{position:absolute;top:165px;width:22px;height:22px;border-radius:50%;background:var(--slate);display:flex;align-items:center;justify-content:center}
.arrow.left{left:10px}.arrow.right{right:10px}

.about{text-align:center;padding-top:40px}
.section-title{font-size:22px;font-weight:300;letter-spacing:1px;color:var(--ink);text-transform:uppercase;position:relative;display:inline-block}
.section-title::before,.section-title::after{content:"";position:absolute;top:50%;width:190px;height:1px;background:var(--rule)}
.section-title::before{right:calc(100% + 14px)}
.section-title::after{left:calc(100% + 14px)}
.about-text{width:580px;margin:14px auto 0;font-size:8.5px;line-height:13px;color:var(--muted)}
.read-more{display:inline-block;margin-top:10px;font-size:8px;font-weight:700;color:var(--blue)}

.features{display:flex;width:628px;margin:30px auto 0}
.feature{flex:1 1 0;min-width:0;height:150px;position:relative;padding:48px 14px 0;text-align:center;color:var(--white)}
.feature.blue{background:var(--blue)}
.feature.dark{background:var(--slate)}
.feature-icon{position:absolute;left:50%;top:-20px;transform:translateX(-50%);width:44px;height:44px;border-radius:50%;border:3px solid var(--white);display:flex;align-items:center;justify-content:center}
.feature.blue .feature-icon{background:var(--slate-2)}
.feature.dark .feature-icon{background:var(--blue)}
.feature-title{font-size:8px;font-weight:700;letter-spacing:.5px;margin-bottom:8px}
.feature-text{font-size:7.5px;line-height:11px;color:#eef4f8}

.testimonials{text-align:center;padding-top:36px}
.quotes{display:flex;justify-content:center;gap:40px;margin-top:22px;text-align:left}
.quote{display:flex;gap:14px;width:300px}
.avatar{flex:0 0 46px;height:58px;background:linear-gradient(#dfe4ea,#b8c0c9)}
.quote-text{font-size:7.5px;line-height:12px;color:var(--muted);font-style:italic}
.quote .who{display:block;margin-top:6px;font-style:normal;font-size:7px;font-weight:700;color:var(--blue)}
.dots{display:flex;justify-content:center;gap:5px;margin-top:16px}
.dots i{width:5px;height:5px;border-radius:50%;background:#c8ccd1}
.dots i.on{background:var(--blue)}

.footer{position:absolute;left:0;right:0;top:1011px;height:189px;background:var(--footer);color:#c2c7cd}
.footer-cols{display:flex;gap:26px;padding:18px 70px 0}
.footer h4{font-size:9px;font-weight:600;color:var(--white);letter-spacing:.5px;margin-bottom:10px}
.news{width:150px}
.news-item{display:flex;gap:8px;margin-bottom:10px}
.news-thumb{flex:0 0 30px;height:24px;background:linear-gradient(#4d5560,#69727d)}
.news-item p{font-size:7px;line-height:10px}
.news-item b{display:block;color:var(--white);font-weight:600}
.links{width:140px}
.links ul{list-style:none;display:grid;grid-template-columns:1fr 1fr;gap:5px 10px;font-size:7px}
.contact{width:140px;font-size:7px;line-height:11px}
.contact-row{display:flex;gap:6px;margin-bottom:8px}
.contact-row svg{flex:0 0 9px;margin-top:1px}
.location{width:120px}
.map{height:82px;background:linear-gradient(135deg,#e9e4d8,#d6dfe3)}
.footer-bottom{position:absolute;left:0;right:0;bottom:0;height:22px;background:var(--footer-2);display:flex;justify-content:center;align-items:center;font-size:7px;color:#8a9098}
.to-top{position:absolute;right:14px;top:6px;font-size:7px;color:#8a9098}
</style>
</head>
<body>

<div class="topbar"><a href="#">LOGIN</a><span>|</span><a href="#">CREATE AN ACCOUNT</a></div>

<header class="header">
  <div class="brand"><span class="brand-dot"></span><span class="brand-name">Greenway Compounding</span></div>
  <nav class="nav">
    <a class="active" href="#"><svg width="14" height="13" viewBox="0 0 14 13"><path d="M7 1 1 6.5h2V12h3V8.5h2V12h3V6.5h2z" fill="#fff"/></svg>HOME</a>
    <a href="#">ABOUT US</a>
    <a href="#">LOCATIONS</a>
    <a href="#">THINGS</a>
    <a href="#">CONTACT</a>
  </nav>
</header>

<section class="hero">
  <div class="hero-photo" role="img" aria-label="Laboratory photo of test tubes with red samples in a rack"></div>
  <div class="hero-copy">
    <p>To provide an awareness of where we are, that we are in the specialty business of compounding pharmacy ... and we want people to contact and visit our physical store.</p>
    <a class="btn" href="#">CLICK MORE INFORMATION</a>
  </div>
  <a class="arrow left" href="#" aria-label="Previous"><svg width="8" height="8" viewBox="0 0 8 8"><path d="M5.5 1 2.5 4l3 3" stroke="#fff" stroke-width="1.6" fill="none"/></svg></a>
  <a class="arrow right" href="#" aria-label="Next"><svg width="8" height="8" viewBox="0 0 8 8"><path d="M2.5 1l3 3-3 3" stroke="#fff" stroke-width="1.6" fill="none"/></svg></a>
</section>

<section class="about">
  <h2 class="section-title">What is Compounding Pharmacy?</h2>
  <p class="about-text">Made ready for a healthier you. Compounding is the practice of preparing medicines tailored to the unique needs of each patient, from adjusted strengths to allergy-free bases and flavoured liquids. Our purpose built laboratory and trained pharmacists prepare every formula with care, serving patients, prescribers and veterinary clients across our local community every day.</p>
  <a class="read-more" href="#">READ MORE &#9656;</a>

  <div class="features">
    <div class="feature blue">
      <div class="feature-icon"><svg width="20" height="18" viewBox="0 0 20 18"><rect x="1" y="4" width="18" height="13" rx="2" fill="#fff"/><rect x="7" y="1" width="6" height="4" rx="1" fill="none" stroke="#fff" stroke-width="1.5"/><path d="M10 7.5v7M6.5 11h7" stroke="#3a424d" stroke-width="2"/></svg></div>
      <h3 class="feature-title">WE DO COMPOUNDING</h3>
      <p class="feature-text">Custom medicines made in our own lab, matched to the dose, form and flavour your prescriber asks for.</p>
    </div>
    <div class="feature dark">
      <div class="feature-icon"><svg width="14" height="20" viewBox="0 0 14 20"><path d="M7 1a6 6 0 0 0-6 6c0 4.5 6 12 6 12s6-7.5 6-12a6 6 0 0 0-6-6z" fill="#fff"/><circle cx="7" cy="7" r="2.3" fill="#1b8fd0"/></svg></div>
      <h3 class="feature-title">WHERE WE ARE</h3>
      <p class="feature-text">Find our store on the main street, with easy parking close by and friendly staff ready to help you.</p>
    </div>
    <div class="feature blue">
      <div class="feature-icon"><svg width="22" height="16" viewBox="0 0 22 16"><circle cx="11" cy="4.5" r="3.2" fill="#fff"/><path d="M5 15c0-3.5 2.7-5.5 6-5.5s6 2 6 5.5z" fill="#fff"/><circle cx="4" cy="6" r="2.2" fill="#fff"/><circle cx="18" cy="6" r="2.2" fill="#fff"/></svg></div>
      <h3 class="feature-title">WHO WE ARE THERE</h3>
      <p class="feature-text">A small team of pharmacists and technicians with years of training in sterile and non-sterile preparation.</p>
    </div>
    <div class="feature dark">
      <div class="feature-icon"><svg width="18" height="18" viewBox="0 0 18 18"><path d="M4 1.5 6.5 1l1.8 4-2 1.5a10 10 0 0 0 5.2 5.2l1.5-2 4 1.8-.5 2.5C16 15.5 14 17 12 16.5 6.5 15 3 11.5 1.5 6 1 4 2.5 2 4 1.5z" fill="#fff"/></svg></div>
      <h3 class="feature-title">HOW YOU CAN VISIT CONTACT</h3>
      <p class="feature-text">Call us, send a message online or drop in during opening hours to talk about your prescription needs.</p>
    </div>
  </div>
</section>

<section class="testimonials">
  <h2 class="section-title">What Our Customers Say</h2>
  <div class="quotes">
    <div class="quote">
      <div class="avatar" role="img" aria-label="Portrait photo of a customer"></div>
      <p class="quote-text">&ldquo;The team prepared a liquid form of my medicine that my son finally takes without fuss. Service was warm, quick and clearly explained every step.&rdquo;<span class="who">SARAH PRESTON</span></p>
    </div>
    <div class="quote">
      <div class="avatar" role="img" aria-label="Portrait photo of a customer"></div>
      <p class="quote-text">&ldquo;As a vet I rely on them for accurate doses for small animals. Their lab work is careful and they always call back the same day.&rdquo;<span class="who">DAVID MERCER</span></p>
    </div>
  </div>
  <div class="dots"><i class="on"></i><i></i><i></i></div>
</section>

<footer class="footer">
  <div class="footer-cols">
    <div class="news">
      <h4>LATEST NEWS</h4>
      <div class="news-item"><div class="news-thumb" role="img" aria-label="News thumbnail"></div><p><b>New lab opening soon</b>Extended hours for compounded orders.</p></div>
      <div class="news-item"><div class="news-thumb" role="img" aria-label="News thumbnail"></div><p><b>Pet medicine day</b>Ask us about flavoured veterinary doses.</p></div>
    </div>
    <div class="links">
      <h4>QUICK LINKS</h4>
      <ul><li>Home</li><li>Testimonials</li><li>About us</li><li>Privacy Policy</li><li>Locations</li><li>Sitemap</li><li>Things</li><li>Terms</li><li>Contact</li></ul>
    </div>
    <div class="contact">
      <h4>CONTACT US</h4>
      <div class="contact-row"><svg width="9" height="12" viewBox="0 0 14 20"><path d="M7 1a6 6 0 0 0-6 6c0 4.5 6 12 6 12s6-7.5 6-12a6 6 0 0 0-6-6z" fill="#1b8fd0"/></svg><span>GREENWAY COMPOUNDING<br>14 Linden Street, Westbrook<br>NSW 2990</span></div>
      <div class="contact-row"><svg width="9" height="9" viewBox="0 0 18 18"><rect x="1" y="3" width="16" height="12" fill="#1b8fd0"/></svg><span>care@greenwaycompounding.example</span></div>
      <div class="contact-row"><svg width="9" height="9" viewBox="0 0 18 18"><path d="M4 1.5 6.5 1l1.8 4-2 1.5a10 10 0 0 0 5.2 5.2l1.5-2 4 1.8-.5 2.5C16 15.5 14 17 12 16.5 6.5 15 3 11.5 1.5 6 1 4 2.5 2 4 1.5z" fill="#1b8fd0"/></svg><span>(02) 5550 1234</span></div>
    </div>
    <div class="location">
      <h4>OUR LOCATION</h4>
      <div class="map" role="img" aria-label="Street map showing the pharmacy location"></div>
    </div>
  </div>
  <div class="footer-bottom">Copyright &copy; 2024 Greenway Compounding. All Rights Reserved.<span class="to-top">TOP</span></div>
</footer>

</body>
</html>
```